Web Design Project

We have a new games division in the company called "Wimbo 7 Games" they are Cool and really different from anything else in the market. They are being sold to the international market and each product has a promotional video that goes with it and also QR coding on all packaging that will link to the website.
The site is to be fun and appeal to all age groups.

Target Market(s)

Children to Adults 6 -60

Requirements
Must have
• It must be cool and fun and show the quirie side of what we are doing. Images will be attached.
Headings:
Products
About Us
Awards
Large new Product area
Video show
News
Nice to have
• Bright and colorful and a bit of witt

```html
<!DOCTYPE html>
<html lang="en">
<head>
<meta charset="utf-8">
<title>Wimbo 7 Games</title>
<link rel="stylesheet" href="https://fonts.googleapis.com/css2?family=Ubuntu:wght@400;500;700&display=swap">
<style>
:root{
  --orange:#f0582a;
  --red:#e8141c;
  --blue:#2aa3de;
  --footer-blue:#36afe3;
  --nav-yellow:#fde3a4;
  --tab-yellow:#fbbd3b;
  --panel-blue:#cde9f9;
  --text:#3a3a3a;
  --white:#ffffff;
}
*{box-sizing:border-box;margin:0;padding:0}
html,body{width:954px;height:1200px;overflow:hidden;background:var(--white)}
body{position:relative;font-family:"Ubuntu",sans-serif;color:var(--text)}
.abs{position:absolute}
.logo{left:24px;top:18px;font-size:38px;color:var(--blue);font-weight:400;letter-spacing:-0.5px}
.social{top:33px;width:19px;height:19px;border-radius:3px}
.social.s1{left:855px;background:#3b5a9a}
.social.s2{left:880px;background:#5fc3e8}
.social.s3{left:906px;background:#f08a24}
.nav{left:24px;top:74px;width:905px;height:32px;background:var(--nav-yellow);display:flex}
.nav a{display:block;height:32px;line-height:31px;text-align:center;font-size:14px;color:#3a3a3a;text-decoration:none;border-right:1px solid #f6cf76}
.nav a.active{background:var(--tab-yellow);color:var(--blue)}
.search{left:740px;top:81px;width:182px;height:19px;background:var(--white);border-radius:2px}
.search svg{position:absolute;right:5px;top:3px}
.hero-img{left:24px;top:117px;width:564px;height:345px;background:linear-gradient(160deg,#8a4a22 0%,#b56a35 40%,#6b3417 100%)}
.hero-panel{left:588px;top:117px;width:340px;height:345px;background:var(--panel-blue)}
.hero-kicker{left:605px;top:155px;font-size:26px;color:var(--orange);letter-spacing:0.3px}
.hero-title{left:604px;top:180px;font-size:53px;font-weight:700;color:var(--orange);letter-spacing:0.5px}
.hero-text{left:608px;top:254px;width:295px;font-size:14.5px;line-height:19.5px;color:#333}
.btn{background:linear-gradient(#ff2a1e,#d90d12);color:#ffe0a0;text-align:center}
.hero-btn{left:791px;top:409px;width:102px;height:28px;line-height:28px;font-size:14px}
.welcome-title{left:24px;top:478px;font-size:20px;color:var(--blue)}
.welcome-title span{color:var(--orange)}
.welcome-text{left:24px;top:507px;width:905px;font-size:12.6px;line-height:16.5px;color:#333}
.small-btn{left:847px;top:584px;width:66px;height:17px;line-height:17px;font-size:10.5px}
.section-bar{height:24px;background:var(--blue)}
.section-tab{height:31px;background:var(--tab-yellow);font-size:18px;color:var(--red);line-height:31px;padding-left:14px}
.thumb{width:166px;height:129px;border:1px solid #c9c9c9}
.stars{left:28px;top:806px}
.price{left:138px;top:807px;font-size:18px;color:var(--blue)}
.video{left:587px;top:669px;width:342px;height:242px;background:#000}
.video-bar{left:587px;top:893px;width:342px;height:18px;background:#1b1b1b;border-top:2px solid #3a3a3a}
.footer{left:24px;top:1031px;width:905px;height:169px;background:var(--footer-blue)}
.footer-col{top:1058px;list-style:none}
.footer-col li{font-size:12px;line-height:23px;color:var(--white)}
.footer-logo{right:56px;top:1062px;font-size:25px;color:var(--white)}
.copy{right:45px;top:1132px;font-size:12px;color:var(--white);text-align:right;line-height:17px}
</style>
</head>
<body>
<header>
  <div class="abs logo">Wimbo 7 Games</div>
  <span class="abs social s1"></span>
  <span class="abs social s2"></span>
  <span class="abs social s3"></span>
  <nav class="abs nav">
    <a class="active" style="width:73px">Home</a>
    <a style="width:93px">Products</a>
    <a style="width:92px">About Us</a>
    <a style="width:83px">Awards</a>
    <a style="width:188px">Large New Product Area</a>
    <a style="width:107px">Video Show</a>
    <a style="width:70px">News</a>
  </nav>
  <div class="abs search">
    <svg width="13" height="13" viewBox="0 0 13 13"><circle cx="5.5" cy="5.5" r="4" fill="none" stroke="#d9141c" stroke-width="2"/><line x1="8.5" y1="8.5" x2="12" y2="12" stroke="#d9141c" stroke-width="2"/></svg>
  </div>
</header>

<section>
  <div class="abs hero-img" role="img" aria-label="Large white tic-tac-toe board on a wooden deck"></div>
  <div class="abs hero-panel"></div>
  <div class="abs hero-kicker">OUR NEW GAME NAMED</div>
  <div class="abs hero-title">TICTACTOE</div>
  <p class="abs hero-text">Lorem Ipsum is simply dummy text of the printing and typesetting industry. Lorem Ipsum has been the industry's standard dummy text ever since the 1500s, when an unknown printer took a galley of type and scrambled it to make a type specimen book.</p>
  <div class="abs btn hero-btn">Read More</div>
</section>

<section>
  <h2 class="abs welcome-title" style="font-weight:400">Welcome to <span>Wimbo7Games</span></h2>
  <p class="abs welcome-text">Lorem Ipsum is simply dummy text of the printing and typesetting industry. Lorem Ipsum has been the industry's standard dummy text ever since the 1500s, when an unknown printer took a galley of type and scrambled it to make a type specimen book. &nbsp;typesetting industry. Lorem Ipsum has been the industry's standard dummy text ever since the 1500s, when an unknown printer took a galley of type and scrambled it to make a type specimen book. typesetting industry. Lorem Ipsum has been the industry's standard dummy text ever since the 1500s, when an unknown printer took a galley of type and scrambled it to make a type specimen book.</p>
  <div class="abs btn small-btn">Read More</div>
</section>

<section>
  <div class="abs section-bar" style="left:228px;top:620px;width:335px"></div>
  <div class="abs section-tab" style="left:24px;top:616px;width:204px">Browse by Category</div>

  <div class="abs thumb" style="left:24px;top:670px;background:linear-gradient(135deg,#a7d8f2,#1c7fc4)" role="img" aria-label="Blue tic-tac-toe app icon"></div>
  <div class="abs thumb" style="left:210px;top:670px;background:linear-gradient(135deg,#f2f2f2,#cfcfcf)" role="img" aria-label="Black and white tic-tac-toe board with hand placing a piece"></div>
  <div class="abs thumb" style="left:395px;top:670px;background:linear-gradient(135deg,#9fb6d6,#c79a62)" role="img" aria-label="Wooden tic-tac-toe board with glass marbles"></div>
  <div class="abs thumb" style="left:24px;top:854px;background:linear-gradient(135deg,#f4f4f4,#3cb6b0 55%,#e86a8a)" role="img" aria-label="Colourful felt noughts and crosses pieces"></div>
  <div class="abs thumb" style="left:210px;top:854px;background:linear-gradient(160deg,#4d7a2c,#b7dd3e 55%,#9a9a8e)" role="img" aria-label="Child playing with a green outdoor tic-tac-toe tray"></div>
  <div class="abs thumb" style="left:395px;top:854px;background:linear-gradient(135deg,#f6f6f3,#e2ddd2)" role="img" aria-label="Hand drawing tic-tac-toe on paper with a pencil"></div>

  <svg class="abs stars" width="76" height="22" viewBox="0 0 76 22">
    <polygon points="10,1 12.6,7.6 19.5,8 14.2,12.4 16,19.2 10,15.4 4,19.2 5.8,12.4 0.5,8 7.4,7.6" fill="#f6b21f"/>
    <polygon points="36,1 38.6,7.6 45.5,8 40.2,12.4 42,19.2 36,15.4 30,19.2 31.8,12.4 26.5,8 33.4,7.6" fill="#f6b21f"/>
    <polygon points="62,1 64.6,7.6 71.5,8 66.2,12.4 68,19.2 62,15.4 56,19.2 57.8,12.4 52.5,8 59.4,7.6" fill="#d6d6d6"/>
  </svg>
  <div class="abs price">$9.99</div>
</section>

<section>
  <div class="abs section-bar" style="left:790px;top:620px;width:139px"></div>
  <div class="abs section-tab" style="left:586px;top:616px;width:204px">Featured Video</div>
  <div class="abs video" role="img" aria-label="Promotional video player"></div>
  <svg class="abs" style="left:749px;top:771px" width="18" height="18" viewBox="0 0 18 18">
    <g fill="#888"><circle cx="9" cy="2" r="1.6"/><circle cx="14" cy="4" r="1.4"/><circle cx="16" cy="9" r="1.3"/><circle cx="14" cy="14" r="1.2"/><circle cx="9" cy="16" r="1.1"/><circle cx="4" cy="14" r="1"/><circle cx="2" cy="9" r="1"/><circle cx="4" cy="4" r="1.5"/></g>
  </svg>
  <div class="abs video-bar"></div>
  <svg class="abs" style="left:596px;top:898px" width="30" height="10" viewBox="0 0 30 10">
    <rect x="0" y="1" width="2.5" height="8" fill="#ccc"/><rect x="5" y="1" width="2.5" height="8" fill="#ccc"/>
    <polygon points="18,3 21,3 25,0 25,10 21,7 18,7" fill="#ccc"/>
  </svg>
</section>

<footer>
  <div class="abs footer"></div>
  <ul class="abs footer-col" style="left:55px"><li>Products</li><li>About Us</li><li>Awards</li><li>Large New Product Area</li><li>Video Show</li></ul>
  <ul class="abs footer-col" style="left:259px"><li>Products</li><li>About Us</li><li>Awards</li><li>Large New Product</li><li>Video Show</li></ul>
  <ul class="abs footer-col" style="left:444px"><li>Products</li><li>About Us</li><li>Awards</li><li>Large New Product</li><li>Video Show</li></ul>
  <div class="abs footer-logo">Wimbo 7 Games</div>
  <div class="abs copy">© 2012 Wimbo7Games<br>Terms of Service - Privacy Policy - Program Policies</div>
</footer>
</body>
</html>
```